Backpack Accessory company needs product package design

We are a start-up in the San Francisco area called "Vornex". We develop a clip for backpacks that lets outdoor sports enthusiasts clip accessories to the front of their backpack, for example, smartphone, water bottle, wallet and passports. We would like to see designs that communicate the features of the clip (ease of use, secure fit, comfortable, no-slip) and value of having things up front of their backpack (improving security, accessibility and weight distribution). Also how important it is to have these items up front when they bike, hike and travel.
Updates

Target Market(s)

hikers, bikers, outdoor sportsmen and travelers,

Industry/Entity Type

It Company

Font styles to use
Serif
Sans Serif

Requirements
Must have
• logo - see last image. not too expensive to implement. Must present value/importance of the clip for every pack. Design stands out, simple and sells itself.
• The clip is 3"x2"x2". The best would be a clamshell design where the product is seen from the front and the insert can be seen above/front and behind the clip. I'd also accept a newly designed header card 6"w x 5"l unfolded.
Nice to have
• Show flexibility of the clip, which can be used to carry a ZenCam camera, Vornex pouch or any belt loop, belt clip or tactical pouch up front.
Should not have
• too complicated

```html
<!DOCTYPE html>
<html lang="en">
<head>
<meta charset="utf-8">
<title>Vornex Multiway Strap Accessory – Package</title>
<link href="https://fonts.googleapis.com/css2?family=Oswald:wght@600&family=Roboto+Condensed:wght@400&family=Roboto:wght@400;500&display=swap" rel="stylesheet">
<style>
  :root {
    --backdrop: #e4e4e4;
    --panel: #f7f7f7;
    --panel-top: #f2f2f2;
    --ink: #2b2b2b;
    --hairline: #d6d6d6;
    --seam: #e0e0e0;
    --photo-a: #8a7a6a;
    --photo-b: #9aa08a;
    --photo-c: #a9c2bd;
    --photo-d: #7f8b93;
    --product: #55575a;
    --heat-1: #e8541e;
    --heat-2: #f0a21a;
    --heat-3: #6fb84a;
    --heat-4: #d9435a;
    --heat-5: #b58ad0;
    --heat: linear-gradient(120deg, var(--heat-1) 0%, var(--heat-2) 35%, var(--heat-3) 55%, var(--heat-4) 75%, var(--heat-5) 100%);
  }
  html, body {
    margin: 0;
    width: 1200px;
    height: 789px;
    overflow: hidden;
    background: var(--backdrop);
  }
  .dieline {
    position: relative;
    width: 1200px;
    height: 789px;
  }
  .top-panel,
  .side-panel,
  .front-panel {
    position: absolute;
    overflow: hidden;
    box-shadow: 0 14px 32px rgba(0,0,0,.10);
  }
  .top-panel {
    left: 470px;
    top: 40px;
    width: 620px;
    height: 250px;
    background: var(--panel-top);
  }
  .top-panel__seam {
    position: absolute;
    left: 0; right: 0;
    top: 124px;
    height: 2px;
    background: var(--seam);
  }
  .top-panel__brand {
    position: absolute;
    left: 60px;
    top: 160px;
    display: flex;
    align-items: center;
    gap: 8px;
    font-family: "Roboto", sans-serif;
    font-weight: 400;
    font-size: 18px;
    color: var(--ink);
  }
  .top-panel__brand .brand__dot { width: 18px; height: 18px; }
  .top-panel__title {
    position: absolute;
    left: 300px;
    top: 22px;
    margin: 0;
    text-align: center;
    font-family: "Oswald", sans-serif;
    font-weight: 600;
    font-size: 32px;
    line-height: 1.15;
    background: var(--heat);
    -webkit-background-clip: text;
    background-clip: text;
    color: transparent;
  }
  .top-panel__note {
    display: block;
    font-family: "Roboto Condensed", sans-serif;
    font-weight: 400;
    font-size: 24px;
  }
  .side-panel {
    left: 110px;
    top: 290px;
    width: 360px;
    height: 450px;
  }
  .side-panel__photos {
    position: absolute;
    inset: 0;
    background: linear-gradient(90deg,
      var(--photo-a) 0%, var(--photo-a) 24%,
      var(--photo-b) 24%, var(--photo-b) 50%,
      var(--photo-c) 50%, var(--photo-c) 74%,
      var(--photo-d) 74%, var(--photo-d) 100%);
  }
  .side-panel__tagline {
    position: absolute;
    left: 0; right: 0;
    top: 195px;
    text-align: center;
    font-family: "Roboto", sans-serif;
    font-weight: 500;
    font-size: 44px;
    color: #fff;
  }
  .front-panel {
    left: 470px;
    top: 290px;
    width: 620px;
    height: 450px;
    background: var(--panel);
  }
  .brand {
    position: absolute;
    left: 48px;
    top: 52px;
    display: flex;
    align-items: center;
    gap: 12px;
    font-family: "Roboto", sans-serif;
    font-weight: 400;
    font-size: 30px;
    color: var(--ink);
  }
  .brand__dot {
    width: 30px; height: 30px;
    border-radius: 50%;
    background: var(--ink);
  }
  .product-frame {
    position: absolute;
    left: 0; top: 0;
  }
  .product-shot {
    position: absolute;
    left: 50px;
    top: 215px;
    width: 220px;
    height: 160px;
    border-radius: 50%;
    background: radial-gradient(ellipse at 50% 50%, var(--product) 0%, #6e7073 50%, rgba(247,247,247,0) 72%);
  }
  .product-title {
    position: absolute;
    left: 340px;
    top: 60px;
    margin: 0;
    font-family: "Oswald", sans-serif;
    font-weight: 600;
    font-size: 50px;
    line-height: 1.12;
    background: var(--heat);
    -webkit-background-clip: text;
    background-clip: text;
    color: transparent;
  }
  .product-title__note {
    display: block;
    font-family: "Roboto Condensed", sans-serif;
    font-weight: 400;
    font-size: 46px;
  }
</style>
</head>
<body>
  <main class="dieline">
    <section class="top-panel">
      <div class="top-panel__seam"></div>
      <div class="top-panel__brand"><span class="brand__dot"></span>Vornex</div>
      <h2 class="top-panel__title">Multiway Strap Accessory<span class="top-panel__note">(Clip only)</span></h2>
    </section>
    <section class="side-panel">
      <div class="side-panel__photos" role="img" aria-label="Strip of photos showing the clip holding a camera, pouch and gear on backpack straps"></div>
      <div class="side-panel__tagline">it holds all</div>
    </section>
    <section class="front-panel">
      <div class="brand"><span class="brand__dot"></span>Vornex</div>
      <svg class="product-frame" width="620" height="450" viewBox="0 0 620 450">
        <path d="M24 215 C 90 160, 220 160, 270 215 C 315 270, 300 360, 250 410" fill="none" stroke="var(--hairline)" stroke-width="1.5"/>
      </svg>
      <div class="product-shot" role="img" aria-label="Photo of the dark grey multiway strap clip"></div>
      <h1 class="product-title">Multiway<br>Strap<br>Accessory<span class="product-title__note">(Clip only)</span></h1>
    </section>
  </main>
</body>
</html>
```